Business card design and logo needed please help

I need a card for a new plumbing business. i want double sided gloss and on the front i need an attractive logo for my business the incorperates a rhino and plumbing to go with my name aswell as my contact info. logo aswell has to be not out there but remeberable as it will be representing this later to be large Business.Could also incorperate the initials of my buisness being TLC. On the back i want the type of work that i undertake, Plumbing, Maintaince, gasfitting and certification, sanitary drainage and stormwater, drain cleaning, All hot water systems installations and repair , FREE QUOTE is needed to stand out aswell. i like an indate colour design but more then one colour like black and grey or anything.info has to be easy to read that will draw in all types of clients. want a slogan on it saying "Solid On Quality" aswell. Email aswell has changed to make it easier for people. Its now( Tlcadvisory@fernmail.test)
Industry/Entity Type
Business
Contact Information for Business Card
Borlo's Plumbing and Gas Fitting, Dale Marchetti, QBSA No. 48 07 316, ABN No. 74 205 913 480, Email. Borlosplumbingandgasfitting@fernmail.test, Mobile no. 0491 630 578
Logo styles of interest
Pictorial/Combination Logo
Abstract Logo
Character Logo
Look and feel

```html
<!DOCTYPE html>
<html lang="en">
<head>
<meta charset="UTF-8">
<title>Borlo's Plumbing and Gas Fitting – Business Card</title>
<link rel="stylesheet" href="https://fonts.googleapis.com/css2?family=Cabin:wght@500;600&family=Lexend:wght@500&family=Merriweather+Sans:ital,wght@1,500&family=Roboto:wght@700&display=swap">
<style>
  :root {
    --teal: #38a9c9;
    --white: #ffffff;
    --ink: #0d0d0d;
  }
  * { margin: 0; padding: 0; box-sizing: border-box; }
  html, body {
    width: 1200px;
    height: 741px;
    overflow: hidden;
    background: var(--white);
  }
  .card {
    position: relative;
    width: 1200px;
    height: 741px;
    background: var(--white);
    font-family: "Cabin", sans-serif;
  }
  .contact-panel {
    position: absolute;
    left: 0; top: 0;
    width: 481px;
    height: 741px;
    background: var(--teal);
    color: var(--white);
  }
  .business-name {
    position: absolute;
    top: 58px; left: 0;
    width: 100%;
    text-align: center;
    font-weight: 500;
    font-size: 58px;
    line-height: 70px;
    letter-spacing: 1px;
  }
  .licences {
    position: absolute;
    top: 446px; left: 35px;
    font-weight: 600;
    font-size: 38px;
    line-height: 44px;
    white-space: nowrap;
  }
  .mobile {
    position: absolute;
    top: 558px; left: 35px;
    font-family: "Roboto", sans-serif;
    font-weight: 700;
    font-size: 54px;
    line-height: 56px;
    white-space: nowrap;
  }
  .brand-mark {
    position: absolute;
    top: 168px; left: 895px;
    width: 240px;
    text-align: center;
    font-family: "Cabin", sans-serif;
    font-weight: 600;
    font-size: 104px;
    line-height: 110px;
    color: var(--ink);
    letter-spacing: 2px;
  }
  .person-name {
    position: absolute;
    top: 346px; left: 500px;
    width: 682px;
    text-align: center;
    font-family: "Lexend", sans-serif;
    font-weight: 500;
    font-size: 72px;
    line-height: 90px;
    color: var(--ink);
    white-space: nowrap;
  }
  .slogan {
    position: absolute;
    top: 436px; left: 500px;
    width: 682px;
    text-align: center;
    font-family: "Merriweather Sans", sans-serif;
    font-style: italic;
    font-weight: 500;
    font-size: 54px;
    line-height: 70px;
    color: var(--teal);
    white-space: nowrap;
  }
  .email {
    position: absolute;
    top: 622px; left: 517px;
    font-weight: 600;
    font-size: 39px;
    line-height: 50px;
    color: var(--teal);
    white-space: nowrap;
  }
  .email-label { margin-right: 16px; }
</style>
</head>
<body>
  <div class="card">
    <section class="contact-panel">
      <h1 class="business-name">Borlo's<br>Plumbing and<br>Gas Fitting</h1>
      <p class="licences">QBSA No. 48 07 316<br>ABN No. 74 205 913 480</p>
      <p class="mobile">Mobile no.<br>0491 630 578</p>
    </section>

    <div class="brand-mark">TLC</div>

    <h2 class="person-name">Dale Marchetti</h2>
    <p class="slogan">"Solid On Quality"</p>
    <p class="email"><span class="email-label">Email:</span>Tlcadvisory@fernmail.test</p>
  </div>
</body>
</html>
```